Business Card Design Project

This is the first time we use our new logo. We need a business card that we can use both on our institutional corporate relationships and also that works for our staff that deals with consumers directly.

VELUNDA is a new company dedicated to empower consumers and to provide them with the best choices for specialized health care using the latest telemedicine technology (medicine at a distance via videoconference).

We want to print this cards in high quality materials and process. We will like designs that allow us to use UV spot varnish and other techniques that will differentiate us.

We are including Two different versions of Color logos. In addition we are including white over black background logos. Those can be used replacing the black for a color.

Please note this is the first time we will be creating any corporate materials with our new logo and colors.

Target Market(s)

34+ consumers of medium high and high socioeconomic levels.

Industry/Entity Type

Health

Requirements
Must have
• Our logo on its original colors
Should not have
• Any other graphical element or design that is not our logo

```html
<!DOCTYPE html>
<html lang="en">
<head>
<meta charset="utf-8">
<title>VELUNDA business card</title>
<link href="https://fonts.googleapis.com/css2?family=Montserrat:wght@400;700&family=Arimo:wght@400&display=swap" rel="stylesheet">
<style>
  :root {
    --page: #e9e6e2;
    --card-dark: #111214;
    --card-mid: #1d1f23;
    --brand-blue: #1f6ea8;
    --panel-blue: #1b5a85;
    --swoosh-light: #5ab4e0;
    --swoosh-deep: #1a78c2;
    --text-light: #5ab4e0;
    --text-white: #ffffff;
    --brand-teal: #14a39a;
  }
  * { margin: 0; padding: 0; box-sizing: border-box; }
  html, body { width: 1200px; height: 1057px; overflow: hidden; background: var(--page); }
  .canvas { position: relative; width: 1200px; height: 1057px; }
  .card {
    position: absolute; left: 170px; width: 860px; height: 491px; overflow: hidden;
    background: radial-gradient(ellipse at 45% 40%, var(--card-mid), var(--card-dark) 75%);
    box-shadow: 0 6px 18px rgba(0,0,0,0.35);
  }
  .card--front { top: 20px; }
  .card--back { top: 546px; }
  .card__texture { position: absolute; inset: 0; background: linear-gradient(135deg, #1c1e22, #0e0f11); opacity: .6; }
  .card__waves { position: absolute; inset: 0; }
  .brand { position: absolute; display: flex; align-items: center; gap: 16px; }
  .brand__dot { border-radius: 50%; background: var(--brand-teal); }
  .brand__name { font-family: "Montserrat", sans-serif; font-weight: 700; color: var(--brand-blue); letter-spacing: 4px; }
  .card--front .brand { left: 70px; top: 120px; }
  .card--front .brand__dot { width: 40px; height: 40px; }
  .card--front .brand__name { font-size: 64px; }
  .holder { position: absolute; left: 80px; top: 260px; font-family: "Montserrat", sans-serif; color: var(--text-light); }
  .holder__name { font-size: 26px; font-weight: 700; }
  .holder__title { font-size: 18px; font-weight: 400; }
  .holder__address { margin-top: 18px; font-size: 19px; line-height: 1.35; }
  .contacts { position: absolute; right: 40px; top: 150px; list-style: none; font-family: "Arimo", sans-serif; font-size: 20px; color: var(--text-white); }
  .contacts li { display: flex; align-items: center; justify-content: flex-end; gap: 10px; margin-bottom: 8px; }
  .contacts svg { width: 16px; height: 16px; }
  .card--back .brand { left: 0; right: 0; top: 150px; justify-content: center; }
  .card--back .brand__dot { width: 56px; height: 56px; }
  .card--back .brand__name { font-size: 96px; letter-spacing: 6px; }
  .back__web { position: absolute; left: 0; right: 0; top: 320px; text-align: center; font-family: "Arimo", sans-serif; font-size: 30px; letter-spacing: 8px; color: var(--text-light); }
</style>
</head>
<body>
<div class="canvas">
  <section class="card card--front">
    <div class="card__texture" role="img" aria-label="Dark woven carbon fibre texture"></div>
    <svg class="card__waves" viewBox="0 0 860 491" aria-hidden="true">
      <path d="M780 0 C640 70 620 290 440 400 C340 460 220 480 110 491 L860 491 L860 0 Z" fill="var(--panel-blue)"/>
      <path d="M760 0 C620 80 590 290 410 395 C320 448 200 470 90 478" fill="none" stroke="var(--swoosh-deep)" stroke-width="10"/>
      <path d="M640 250 C560 360 420 420 240 452 C180 462 120 470 60 472 C180 470 360 452 480 410 C560 380 610 320 640 250 Z" fill="var(--swoosh-light)"/>
    </svg>
    <div class="brand">
      <span class="brand__dot"></span>
      <span class="brand__name">VELUNDA</span>
    </div>
    <div class="holder">
      <p><span class="holder__name">Your Name,</span> <span class="holder__title">Title</span></p>
      <p class="holder__address">Street Name, City Name<br>State, City Zip Code</p>
    </div>
    <ul class="contacts">
      <li><svg viewBox="0 0 16 16"><path d="M4 1 L6 5 L4.5 6.5 C5.5 8.5 7.5 10.5 9.5 11.5 L11 10 L15 12 L13.5 15 C7 15 1 9 1 2.5 Z" fill="#fff"/></svg>010-555-0147</li>
      <li><svg viewBox="0 0 16 16"><path d="M4 1 L6 5 L4.5 6.5 C5.5 8.5 7.5 10.5 9.5 11.5 L11 10 L15 12 L13.5 15 C7 15 1 9 1 2.5 Z" fill="#fff"/></svg>010-555-0147</li>
      <li><svg viewBox="0 0 16 16"><rect x="1" y="3" width="14" height="10" fill="#fff"/><path d="M1 3 L8 9 L15 3" fill="none" stroke="var(--panel-blue)" stroke-width="1.5"/></svg>name@velunda.com</li>
      <li><svg viewBox="0 0 16 16"><circle cx="8" cy="8" r="7" fill="none" stroke="#fff" stroke-width="1.5"/><ellipse cx="8" cy="8" rx="3" ry="7" fill="none" stroke="#fff" stroke-width="1.2"/><path d="M1 8 H15" stroke="#fff" stroke-width="1.2"/></svg>www.velunda.com</li>
    </ul>
  </section>

  <section class="card card--back">
    <div class="card__texture" role="img" aria-label="Dark woven carbon fibre texture"></div>
    <div class="brand">
      <span class="brand__dot"></span>
      <span class="brand__name">VELUNDA</span>
    </div>
    <p class="back__web">www.velunda.com</p>
  </section>
</div>
</body>
</html>
```